Heron Dusk business card design

I make handmade colourful women's beaded jewellery (necklaces and earnings).
I require a business card to be designed to truly reflect my jewellery, that is, it is different and stands out.
I would like the business card to look creative, arty, gentle and feminine and fit in with the look of my website and logo (already developed).
I would like the business card to have strong use of the water reeds that are flowing in the wind (please see the banner image on my website www.herondusk.net and attached files).

Target Market(s)

Women who are fashion conscious, hip and funky. My audience like things that are a little different and stand out in a crowd.These women are aged in their 20's-40's.

Industry/Entity Type

Jewelry

Contact Information for Business Card

Please include the following items:
1) my logo: Heron Dusk
2) my name, address and phone number: Darla Fontenot, Sydney, Australia, 0498 315 270
3) my web details: www.herondusk.net, info@herondusk.net, www.facebook.com/herondusk

Font styles to use
Other font styles liked:
• Remachine Script

Requirements
Must have
• My business card must have the following:
• 1) my personal details including all my website contacts (see above).
• 2) Heron Dusk logo
• 3) Reeds flowing in the wind (see my banner image on my website www.herondusk.net or see attached files).
Nice to have
• A sunrise in the background (rising over water)
• I would prefer that the colour scheme to fit with the Heron Dusk logo, that is the colours of an early morning sunrise i.e yellows, oranges. The use of black and white is fine.
Should not have
• I do not like a commercial manufactured look with hard edges. I would like a look that is soft and reflects an artistic, creative and independent business.

```html
<!DOCTYPE html>
<html lang="en">
<head>
<meta charset="utf-8">
<title>Heron Dusk — Business Card</title>
<link rel="stylesheet" href="https://fonts.googleapis.com/css2?family=Kalam:wght@400&family=Noto+Serif:wght@400&display=swap">
<style>
  :root {
    --backdrop: #8e8e8e;
    --paper: #f3f3f5;
    --ink: #1b1b1b;
    --sun-core: #f2c40f;
    --sun-mid: #f0a81c;
    --sun-edge: #e8891a;
    --glow: #f6b53a;
    --accent: #e9a21c;
  }
  * { box-sizing: border-box; margin: 0; padding: 0; }
  html, body {
    width: 1105px;
    height: 1200px;
    overflow: hidden;
    background: var(--backdrop);
  }
  .card {
    position: absolute;
    left: 180px;
    width: 745px;
    height: 428px;
    background: var(--paper);
    overflow: hidden;
  }
  .card--front { top: 120px; }
  .card--back { top: 655px; }

  .sun-art {
    position: absolute;
    left: 0;
    top: 0;
    width: 745px;
    height: 428px;
  }

  .contact {
    position: absolute;
    left: 44px;
    top: 228px;
    font-family: "Noto Serif", serif;
    font-size: 19px;
    color: var(--ink);
    line-height: 1;
  }
  .contact__line {
    display: flex;
    align-items: center;
    height: 29px;
  }
  .contact__line--icon { height: 34px; }
  .contact__icon {
    width: 16px;
    height: 16px;
    margin-left: 4px;
    margin-right: 15px;
    flex: none;
  }

  .brand {
    position: absolute;
    display: flex;
    flex-direction: column;
    align-items: center;
  }
  .brand__name {
    font-family: "Kalam", cursive;
    font-size: 40px;
    color: var(--ink);
    line-height: 1.1;
    white-space: nowrap;
  }
  .brand__disc {
    border-radius: 50%;
    background: radial-gradient(circle at 50% 40%, var(--sun-core), var(--sun-mid) 60%, var(--sun-edge));
    border: 4px solid var(--ink);
  }
  .card--front .brand { left: 488px; top: 36px; width: 200px; }
  .card--front .brand__disc { width: 168px; height: 168px; margin-top: 6px; }
  .card--back .brand { left: 242px; top: 60px; width: 260px; }
  .card--back .brand__name { font-size: 46px; }
  .card--back .brand__disc { width: 204px; height: 204px; margin-top: 8px; }

  .holder {
    position: absolute;
    left: 487px;
    top: 303px;
    font-family: "Kalam", cursive;
    line-height: 1.15;
  }
  .holder__name {
    font-size: 34px;
    color: var(--ink);
  }
  .holder__role {
    margin-left: 44px;
    font-size: 22px;
    color: var(--accent);
  }
</style>
</head>
<body>

<section class="card card--front" aria-label="Business card front">
  <svg class="sun-art" viewBox="0 0 745 428" aria-hidden="true">
    <defs>
      <radialGradient id="sun-glow" cx="148" cy="367" r="400" gradientUnits="userSpaceOnUse">
        <stop offset="0" stop-color="var(--glow)" stop-opacity="1"/>
        <stop offset="0.55" stop-color="var(--glow)" stop-opacity="0.75"/>
        <stop offset="1" stop-color="var(--glow)" stop-opacity="0"/>
      </radialGradient>
      <radialGradient id="sun-disc" cx="180" cy="300" r="240" gradientUnits="userSpaceOnUse">
        <stop offset="0" stop-color="var(--sun-core)"/>
        <stop offset="0.6" stop-color="var(--sun-mid)"/>
        <stop offset="1" stop-color="var(--sun-edge)"/>
      </radialGradient>
    </defs>
    <rect width="745" height="428" fill="url(#sun-glow)"/>
    <circle cx="148" cy="367" r="218" fill="url(#sun-disc)" stroke="var(--ink)" stroke-width="3.5"/>
  </svg>

  <div class="contact">
    <p class="contact__line">Darla Fontenot</p>
    <p class="contact__line">Sydney, Australia</p>
    <p class="contact__line contact__line--icon">
      <svg class="contact__icon" viewBox="0 0 16 16" aria-hidden="true"><path d="M3.2 1.2l2.6 2.6-1.6 2.2c.9 2 2.6 3.7 4.6 4.6l2.2-1.6 2.6 2.6-1.8 2.6C6.8 14 2 9.2 .6 3z" fill="var(--ink)"/></svg>
      0498 315 270
    </p>
    <p class="contact__line contact__line--icon">
      <svg class="contact__icon" viewBox="0 0 16 16" aria-hidden="true"><rect x="1" y="3.5" width="14" height="9" fill="var(--ink)"/><path d="M1.5 4l6.5 5 6.5-5" fill="none" stroke="var(--paper)" stroke-width="1.2"/></svg>
      info@herondusk.net
    </p>
    <p class="contact__line contact__line--icon">
      <svg class="contact__icon" viewBox="0 0 16 16" aria-hidden="true"><circle cx="8" cy="8" r="7" fill="var(--ink)"/><path d="M1 8h14M8 1c-3 3.5-3 10.5 0 14M8 1c3 3.5 3 10.5 0 14" fill="none" stroke="var(--sun-mid)" stroke-width="1"/></svg>
      www.herondusk.net
    </p>
  </div>

  <div class="brand">
    <span class="brand__name">Heron Dusk</span>
    <span class="brand__disc" role="img" aria-label="Brand emblem area: heron silhouette on a post with reeds before a rising sun over water"></span>
  </div>

  <div class="holder">
    <p class="holder__name">Marcus Hale</p>
    <p class="holder__role">CEO/Founder</p>
  </div>
</section>

<section class="card card--back" aria-label="Business card back">
  <div class="brand">
    <span class="brand__name">Heron Dusk</span>
    <span class="brand__disc" role="img" aria-label="Brand emblem area: heron silhouette on a post with reeds before a rising sun over water"></span>
  </div>
</section>

</body>
</html>
```